Website design with eCommerce for revolutionary new product in the manufacturing industry.

We need a website designed for a precision manufacturing company based in the suburbs of Minneapolis, Minnesota called Velkrin Manufacturing. We have a revolutionary new product, the TARN LOCK, to introduce and sell through an eCommerce storefront. The website would include company information, product information, and the storefront. Green is a color that represents Velkrin Manufacturing. The final design should communicate that we exclusively offer premium products at a premium price. The design should also let the customer know they are the focus of our work.

Target Market(s)

Machinists and machine shops

Industry/Entity Type

Manufacturing and machine shops

Coding

Coded - Design and coding required

Font styles to use
Sans Serif

Colors
59FF00
82FF00
B8FF75
E3FFCB
F4FFEA

Requirements
Must have
• eCommerce storefront, Made in USA references
Nice to have
• Home page, TARN LOCK Product page, About Us, Capabilities, Contact, etc.
Should not have
• Should not be too much text and reading.

```html
<!DOCTYPE html>
<html lang="en">
<head>
<meta charset="utf-8">
<title>Contact — TARN LOCK</title>
<link href="https://fonts.googleapis.com/css2?family=Poppins:wght@400;500;600;700;800&display=swap" rel="stylesheet">
<style>
:root{
  --green:#59ff00;
  --ink:#111111;
  --dark:#1b1b1b;
  --field:#e8e8e8;
  --field-dark:#2e2e2e;
  --muted:#555;
  --white:#ffffff;
}
*{margin:0;padding:0;box-sizing:border-box}
html,body{width:672px;height:1200px;overflow:hidden}
body{position:relative;background:var(--white);font-family:'Poppins',sans-serif;color:var(--ink)}
.abs{position:absolute}
.site-header{left:0;top:0;width:672px;height:43px;background:var(--white);z-index:3}
.brand{left:50px;top:12px;font-weight:800;font-size:15px;letter-spacing:.5px;color:var(--ink);display:flex;align-items:center;gap:5px}
.brand .mark{width:9px;height:9px;background:var(--ink)}
.nav{left:178px;top:17px;display:flex;gap:11px;font-size:6.6px;font-weight:500;text-transform:uppercase}
.nav-cta{left:616px;top:0;width:56px;height:43px;background:var(--green);font-size:7px;font-weight:700;display:flex;align-items:center;justify-content:center}
.hero{left:0;top:43px;width:672px;height:222px}
.hero-title{left:0;top:105px;width:672px;text-align:center;color:var(--white);font-weight:800;font-size:33px;letter-spacing:1px}
.section-title{left:0;top:275px;width:672px;text-align:center;font-weight:800;font-size:22px}
.title-rule{left:313px;top:306px;width:34px;height:2px;background:var(--green)}
.lead{left:0;top:320px;width:672px;text-align:center;font-size:8px;color:#333}
.info-item{left:111px;display:flex;align-items:center;gap:9px}
.info-icon{width:37px;height:37px;background:var(--green);border-radius:3px;display:flex;align-items:center;justify-content:center}
.info-label{font-size:11px;line-height:1.2}
.info-value{font-size:12.5px;font-weight:700;line-height:1.2}
.lbl{font-size:5.8px;font-weight:600;text-transform:uppercase}
.field{background:var(--field);border-radius:2px;font-size:6.5px;color:#777;padding:0 8px;display:flex;align-items:center}
.submit{left:339px;top:537px;width:226px;height:27px;background:var(--green);border-radius:2px;display:flex;align-items:center;justify-content:center;font-weight:700;font-size:8.5px}
.submit svg{position:absolute;right:11px;top:8px}
.map-card{left:105px;top:619px;width:464px;height:212px;background:var(--white);box-shadow:0 4px 16px rgba(0,0,0,.1);border-radius:3px}
.map{left:5px;top:5px;width:454px;height:202px;background:linear-gradient(135deg,#e2e2e2,#d2d2d2 55%,#c9c9c9);border-radius:2px}
.footer{left:0;top:894px;width:672px;height:306px;background:var(--dark);color:var(--white)}
.footer-brand{left:50px;top:925px;color:var(--white);font-size:15px}
.footer-brand .mark{background:var(--white)}
.footer-about{left:199px;top:920px;width:150px;font-size:8px;line-height:1.55;color:var(--white)}
.callbar{left:443px;top:927px;display:flex;align-items:center;gap:6px}
.call-icon{width:25px;height:25px;background:var(--dark);display:flex;align-items:center;justify-content:center}
.call-label{font-size:7.5px;font-weight:600;margin-top:4px}
.call-num{font-size:15px;font-weight:700}
.fcol h4{font-size:10px;font-weight:700;color:var(--white);margin-bottom:9px}
.links li{list-style:none;font-size:6.5px;line-height:12.5px;color:var(--white)}
.social li{list-style:none;display:flex;align-items:center;gap:5px;font-size:6.5px;height:20px}
.social .sq{width:14px;height:14px;background:#333;border-radius:2px}
.contact-li{display:flex;gap:5px;font-size:7px;line-height:11px;margin-bottom:8px}
.fin{left:451px;width:146px;height:19px;background:var(--field-dark);font-size:6.5px;color:#ccc;padding:0 8px;display:flex;align-items:center;border-radius:1px}
.fsubmit{left:451px;top:1106px;width:52px;height:20px;background:var(--white);color:var(--ink);font-size:7px;font-weight:700;display:flex;align-items:center;justify-content:center;border-radius:1px}
.frule{left:51px;top:1167px;width:575px;height:1px;background:#3a3a3a}
.copy{left:0;top:1181px;width:672px;text-align:center;font-size:7px;font-weight:600;color:var(--white)}
.totop{left:636px;top:1156px;width:26px;height:25px;background:var(--green);display:flex;align-items:center;justify-content:center}
</style>
</head>
<body>

<header class="abs site-header">
  <div class="abs brand"><span class="mark"></span>TARN LOCK</div>
  <nav class="abs nav">
    <span>Why Velkrin Manufacturing?</span><span>What We Do</span><span>How We Make It Better</span><span>Capabilities</span><span>Gallery</span><span>About Us</span><span>Wisdom</span>
  </nav>
  <div class="abs nav-cta">CONTACT</div>
</header>

<svg class="abs hero" viewBox="0 43 672 222" role="img" aria-label="Close-up photograph of machined steel parts">
  <defs>
    <linearGradient id="steel" x1="0" y1="0" x2="1" y2="1">
      <stop offset="0" stop-color="#6f6a63"/>
      <stop offset=".5" stop-color="#8e8b86"/>
      <stop offset="1" stop-color="#5d5852"/>
    </linearGradient>
  </defs>
  <rect x="0" y="43" width="672" height="222" fill="url(#steel)"/>
  <polygon points="0,262 672,186 672,265 0,265" fill="#ffffff"/>
  <polygon points="15,260 672,157 672,186 0,262" fill="#59ff00"/>
</svg>
<h1 class="abs hero-title">CONTACT</h1>

<h2 class="abs section-title">GET IN TOUCH</h2>
<div class="abs title-rule"></div>
<p class="abs lead">Please fill out the information below to complete...</p>

<div class="abs info-item" style="top:368px">
  <div class="info-icon"><svg width="16" height="16" viewBox="0 0 24 24"><path fill="#111" d="M6.6 10.8a15 15 0 0 0 6.6 6.6l2.2-2.2a1 1 0 0 1 1-.25 11.4 11.4 0 0 0 3.6.57 1 1 0 0 1 1 1V20a1 1 0 0 1-1 1A17 17 0 0 1 3 4a1 1 0 0 1 1-1h3.5a1 1 0 0 1 1 1c0 1.25.2 2.45.57 3.57a1 1 0 0 1-.25 1z"/></svg></div>
  <div><div class="info-label">Phone:</div><div class="info-value">123 4567 655</div></div>
</div>
<div class="abs info-item" style="top:420px">
  <div class="info-icon"><svg width="16" height="14" viewBox="0 0 24 20"><path fill="#111" d="M2 2h20v3l-10 6L2 5zM2 8l10 6 10-6v10H2z"/></svg></div>
  <div><div class="info-label">Email:</div><div class="info-value">info@tarnlock.com</div></div>
</div>
<div class="abs info-item" style="top:472px">
  <div class="info-icon"><svg width="14" height="18" viewBox="0 0 24 30"><path fill="#111" d="M12 0a10 10 0 0 0-10 10c0 8 10 20 10 20s10-12 10-20A10 10 0 0 0 12 0zm0 14a4 4 0 1 1 0-8 4 4 0 0 1 0 8z"/></svg></div>
  <div><div class="info-label">Address:</div><div class="info-value">Some goes address here</div></div>
</div>

<form>
  <span class="abs lbl" style="left:337px;top:367px">Name*</span>
  <span class="abs lbl" style="left:453px;top:367px">Email*</span>
  <div class="abs field" style="left:339px;top:378px;width:110px;height:23px">Enter your name</div>
  <div class="abs field" style="left:453px;top:378px;width:111px;height:23px">Enter your email</div>
  <span class="abs lbl" style="left:337px;top:406px">Phone*</span>
  <span class="abs lbl" style="left:453px;top:406px">Date*</span>
  <div class="abs field" style="left:339px;top:417px;width:110px;height:23px">Enter phone number</div>
  <div class="abs field" style="left:453px;top:417px;width:111px;height:23px;justify-content:space-between;padding-left:10px">Select date
    <svg width="6" height="4" viewBox="0 0 6 4"><path d="M.5.5 3 3 5.5.5" stroke="#111" fill="none"/></svg></div>
  <span class="abs lbl" style="left:337px;top:448px">Phone*</span>
  <div class="abs field" style="left:339px;top:458px;width:226px;height:63px;align-items:flex-start;padding-top:9px">Type your text...</div>
  <div class="abs submit">SUBMIT NOW
    <svg width="11" height="10" viewBox="0 0 24 22"><path fill="#111" d="M23 0 0 10l7 3 12-9-9 11v7l4-5 6 3z"/></svg></div>
</form>

<div class="abs map-card">
  <div class="abs map" role="img" aria-label="Street map showing the company location"></div>
</div>

<footer class="abs footer"></footer>
<svg class="abs" style="left:0;top:894px" width="672" height="70" viewBox="0 894 672 70">
  <polygon points="361,894 672,894 672,914 370,914" fill="#ffffff"/>
  <polygon points="370,914 672,914 672,963 392,963" fill="#59ff00"/>
</svg>
<div class="abs brand footer-brand"><span class="mark"></span>TARN LOCK</div>
<p class="abs footer-about">Velkrin Manufacturing has humble roots, starting as many machine</p>
<div class="abs callbar">
  <div class="call-icon"><svg width="11" height="11" viewBox="0 0 24 24"><path fill="#fff" d="M6.6 10.8a15 15 0 0 0 6.6 6.6l2.2-2.2a1 1 0 0 1 1-.25 11.4 11.4 0 0 0 3.6.57 1 1 0 0 1 1 1V20a1 1 0 0 1-1 1A17 17 0 0 1 3 4a1 1 0 0 1 1-1h3.5a1 1 0 0 1 1 1c0 1.25.2 2.45.57 3.57a1 1 0 0 1-.25 1z"/></svg></div>
  <span class="call-label">Call us:</span><span class="call-num">+123 456 7890</span>
</div>

<div class="abs fcol" style="left:81px;top:1004px">
  <h4>Helpful Links</h4>
  <ul class="links"><li>Why Velkrin Manufacturing?</li><li>What We Do</li><li>How We Make It Better</li><li>Capabilities</li><li>Gallery</li><li>About Us</li><li>Wisdom</li><li>Contact Us</li></ul>
</div>
<div class="abs fcol" style="left:211px;top:1004px">
  <h4>Information</h4>
  <ul class="social"><li><span class="sq"></span>Facebook</li><li><span class="sq"></span>Twitter</li><li><span class="sq"></span>Google</li><li><span class="sq"></span>Linkedin</li><li><span class="sq"></span>Youtube</li></ul>
</div>
<div class="abs fcol" style="left:315px;top:1004px">
  <h4>Contact Us</h4>
  <div class="contact-li" style="margin-top:13px"><svg width="7" height="6" viewBox="0 0 24 20"><path fill="#59ff00" d="M2 2h20v3l-10 6L2 5zM2 8l10 6 10-6v10H2z"/></svg><div>Email:<br>info@tarnlock.com</div></div>
  <div class="contact-li"><svg width="7" height="7" viewBox="0 0 24 24"><path fill="#59ff00" d="M6.6 10.8a15 15 0 0 0 6.6 6.6l2.2-2.2a1 1 0 0 1 1-.25 11.4 11.4 0 0 0 3.6.57 1 1 0 0 1 1 1V20a1 1 0 0 1-1 1A17 17 0 0 1 3 4a1 1 0 0 1 1-1h3.5a1 1 0 0 1 1 1c0 1.25.2 2.45.57 3.57a1 1 0 0 1-.25 1z"/></svg><div>Phone:<br>+08 123 456 7890</div></div>
  <div class="contact-li"><svg width="6" height="8" viewBox="0 0 24 30"><path fill="#59ff00" d="M12 0a10 10 0 0 0-10 10c0 8 10 20 10 20s10-12 10-20A10 10 0 0 0 12 0zm0 14a4 4 0 1 1 0-8 4 4 0 0 1 0 8z"/></svg><div>Location:<br>Some address line goes<br>here city name</div></div>
</div>
<div class="abs fcol" style="left:450px;top:1004px"><h4>Get in Touch</h4></div>
<div class="abs fin" style="top:1032px">Enter Name</div>
<div class="abs fin" style="top:1055px">Enter Company</div>
<div class="abs fin" style="top:1078px">Enter Country</div>
<div class="abs fsubmit">SUBMIT</div>

<div class="abs totop"><svg width="6" height="9" viewBox="0 0 6 9"><path d="M3 9V1M.5 3.5 3 1l2.5 2.5" stroke="#111" fill="none" stroke-width=".8"/></svg></div>
<div class="abs frule"></div>
<p class="abs copy">©COPYRIGHT 2022 TARN LOCK, ALL RIGHTS RESERVED</p>

</body>
</html>
```